New Business Card Design for Manufacturing

We are an engineering/manufacturing company that offers Advanced machining/assembly/engineering services, as well as innovative products for the heavy duty engine cooling markets.

We are looking to get a new business card designed that is clean and modern looking, but still fits the wide range of technical/skilled work we do.

- We hope to use this design as the base for other design work in new Presentations, web, and print work.

Industry/Entity Type

Engineering

Contact Information for Business Card

Our preferred color of blue is (RGB) 22/71/159 but can vary slightly from that color. Our content will be our Logo and full company name (Vantrell Forge Works, Inc.), company address, name, job title, phone number with extension, cell number, fax number, website, and email address on the cards.
We'd like the full company name next to the logo, but we are open to other interpretations of that layout.
Preferably, we would like the back side to be clean with just our logo, and the front to contain all of the contact information.

Colors
2f74b4
0355a3
85abd2

Requirements
Must have
• - Logo, company name, needed content - We are open to interpretation beyond that.
• - Standard size business card.
• - Horizontal orientation.
• - Enough space for lengthy names / job titles (for example, a job title could read "Directory of Human Resources" or "V.P. of Governmental Affairs"). We need this to look clean, whether the title be short (CEO) or long (as described above).

```html
<!DOCTYPE html>
<html lang="en">
<head>
<meta charset="utf-8">
<title>Vantrell Forge Works – Business Card</title>
<link rel="stylesheet" href="https://fonts.googleapis.com/css2?family=Roboto:wght@400;500;700;900&display=swap">
<style>
  :root {
    --backdrop: #3b3430;
    --card: #17181b;
    --card-edge: #0d0d0f;
    --brand-blue: #2f74b4;
    --brand-blue-deep: #0355a3;
    --brand-blue-light: #85abd2;
    --text-light: #e6e7ea;
    --text-muted: #b9bcc2;
    --silver: #6d7078;
  }
  * { margin: 0; padding: 0; box-sizing: border-box; }
  html, body { width: 1200px; height: 716px; overflow: hidden; }
  body {
    background: var(--backdrop);
    font-family: "Roboto", Arial, sans-serif;
    position: relative;
  }
  .card {
    position: absolute;
    top: 215px;
    width: 500px;
    height: 286px;
    background: var(--card);
    border: 1px solid var(--card-edge);
    box-shadow: 0 10px 24px rgba(0,0,0,.45);
  }
  .card--back { left: 70px; }
  .card--front { left: 630px; }

  /* Back side */
  .back-lockup {
    position: absolute;
    left: 50px;
    top: 104px;
    display: flex;
    align-items: center;
    gap: 18px;
  }
  .back-mark {
    display: flex;
    align-items: center;
    gap: 10px;
    font-weight: 900;
    font-size: 34px;
    letter-spacing: 1px;
    color: var(--silver);
    text-transform: uppercase;
  }
  .back-mark .mark-square {
    width: 18px; height: 18px;
    background: var(--silver);
  }
  .company-name {
    font-weight: 700;
    font-size: 17px;
    line-height: 1.05;
    color: var(--text-light);
    text-transform: uppercase;
    letter-spacing: .5px;
  }
  .company-name small {
    font-size: 9px;
    font-weight: 500;
    margin-left: 2px;
  }

  /* Front side */
  .accent-bar {
    position: absolute;
    left: 0; top: 34px;
    width: 8px; height: 38px;
    background: var(--brand-blue);
  }
  .contact {
    position: absolute;
    left: 34px; top: 34px;
    color: var(--text-light);
  }
  .person-name {
    font-size: 19px;
    font-weight: 500;
    color: var(--brand-blue);
    line-height: 1.1;
  }
  .person-title {
    font-size: 13px;
    color: var(--text-light);
    margin-top: 2px;
  }
  .address {
    font-size: 11.5px;
    line-height: 1.4;
    color: var(--text-muted);
    margin-top: 18px;
  }
  .contact-list {
    list-style: none;
    margin-top: 12px;
    font-size: 11.5px;
    color: var(--text-muted);
  }
  .contact-list li {
    display: flex;
    align-items: center;
    gap: 8px;
    line-height: 1.6;
  }
  .contact-list svg { width: 10px; height: 10px; fill: var(--brand-blue); flex: none; }
  .front-mark {
    position: absolute;
    right: 36px;
    top: 124px;
    display: flex;
    align-items: center;
    gap: 10px;
    font-weight: 900;
    font-size: 32px;
    letter-spacing: 1px;
    color: var(--brand-blue);
    text-transform: uppercase;
  }
  .front-mark .mark-square {
    width: 16px; height: 16px;
    background: var(--brand-blue);
  }
</style>
</head>
<body>

  <section class="card card--back" aria-label="Card back">
    <div class="back-lockup">
      <div class="back-mark"><span class="mark-square"></span>Vantrell</div>
      <div class="company-name">Forge<br>Works<small>Inc</small></div>
    </div>
  </section>

  <section class="card card--front" aria-label="Card front">
    <span class="accent-bar"></span>
    <div class="contact">
      <p class="person-name">Dale Okafor</p>
      <p class="person-title">V.P. of Governmental Affairs</p>
      <p class="address">Level 2, 57 Harlow Street<br>Brenton, VIC 3104</p>
      <ul class="contact-list">
        <li><svg viewBox="0 0 10 10"><path d="M2 0h2l1 3-1.5 1a6 6 0 0 0 2.5 2.5L7 5l3 1v2a2 2 0 0 1-2 2A8 8 0 0 1 0 2a2 2 0 0 1 2-2z"/></svg>555 014 2273</li>
        <li><svg viewBox="0 0 10 10"><rect x="2.5" y="0" width="5" height="10" rx="1"/></svg>555 019 4480</li>
        <li><svg viewBox="0 0 10 10"><path d="M0 2h10v6H0z"/></svg>hello@vantrellforge.com</li>
        <li><svg viewBox="0 0 10 10"><circle cx="5" cy="5" r="5"/></svg>www.vantrellforge.com</li>
      </ul>
    </div>
    <div class="front-mark"><span class="mark-square"></span>Vantrell</div>
  </section>

</body>
</html>
```